KBT Business Cards

We require business cards for our business. We would like a matte black back to the card, with our logo centred in the middle. The front side of the card is open to design.

Target Market(s)

Clients looking for legal services (professional)

Industry/Entity Type

Legal

Contact Information for Business Card

Doran Kelbrath
Partner
Mobile: 0461 738 524
Email: doran@kbtlaw.co
Website: www.kbtlaw.co
Level 3, 118 Wendmore Street
Sydney NSW 2000

Font styles to use
Other font styles liked:
• Avenir

Colors
f04a50
ffffff
1b1b1b

Requirements
Must have
• Black back with logo included in the centre of the card.
• Our font is Avenir.

```html
<!DOCTYPE html>
<html lang="en">
<head>
<meta charset="utf-8">
<title>KBT Business Cards</title>
<link rel="stylesheet" href="https://fonts.googleapis.com/css2?family=Nunito+Sans:wght@400;600;700;800&display=swap">
<style>
  :root {
    --page-bg: #e9e9e9;
    --card-black: #1f1e1f;
    --card-light: #f5f6f8;
    --crimson: #a02342;
    --ink: #1b1b1b;
    --ink-soft: #2b2b2b;
    --emboss: #3b3b3c;
    --white: #ffffff;
  }
  * { box-sizing: border-box; margin: 0; padding: 0; }
  html, body {
    width: 1200px; height: 800px; overflow: hidden;
    background: var(--page-bg);
    font-family: "Nunito Sans", "Avenir", sans-serif;
  }
  .canvas { position: relative; width: 1200px; height: 800px; }

  .card {
    position: absolute; left: 316px; width: 570px; height: 330px;
    border-radius: 18px; overflow: hidden;
  }
  .card--back { top: 50px; background: var(--card-black); }
  .card--front { top: 419px; background: var(--card-light); }

  /* Back: firm name centred */
  .back-name {
    position: absolute; left: 0; right: 0; top: 50%;
    transform: translateY(-50%);
    text-align: center;
    color: var(--emboss);
    font-weight: 800; font-size: 29px; line-height: 1.05;
    letter-spacing: -0.2px; text-transform: uppercase;
  }

  /* Front */
  .firm-name {
    position: absolute; left: 60px; top: 124px;
    color: var(--ink);
    font-weight: 800; font-size: 19px; line-height: 1.08;
    letter-spacing: -0.2px; text-transform: uppercase;
  }
  .divider {
    position: absolute; left: 284px; top: 109px;
    width: 2px; height: 110px; background: var(--crimson);
  }
  .contact { position: absolute; left: 311px; top: 104px; }
  .contact__name {
    color: var(--crimson); font-weight: 700; font-size: 21px; line-height: 1.3;
  }
  .contact__role {
    color: var(--ink); font-weight: 400; font-size: 16px; line-height: 1.4;
    margin-bottom: 4px;
  }
  .contact__list { list-style: none; }
  .contact__item {
    display: flex; align-items: center; gap: 10px;
    color: var(--ink-soft); font-size: 14px; line-height: 21.5px;
  }
  .contact__icon { width: 11px; height: 11px; flex: none; }
  .accent { color: var(--crimson); }

  .address {
    position: absolute; left: 0; right: 0; top: 258px;
    text-align: center; color: var(--ink); font-size: 14px; font-weight: 600;
  }
  .wave { position: absolute; left: 0; top: 0; width: 570px; height: 330px; }
</style>
</head>
<body>
<main class="canvas">
  <section class="card card--back" aria-label="Card back">
    <p class="back-name">Kelbrath<br>Brannock<br>Tate</p>
  </section>

  <section class="card card--front" aria-label="Card front">
    <svg class="wave" viewBox="0 0 570 330" aria-hidden="true">
      <path d="M0,280 Q285,330 570,280 L570,330 L0,330 Z" fill="var(--crimson)"/>
      <path d="M15,277 Q285,322 555,277 Q285,314 15,277 Z" fill="var(--ink)"/>
    </svg>

    <p class="firm-name">Kelbrath<br>Brannock<br>Tate</p>
    <div class="divider"></div>

    <div class="contact">
      <h1 class="contact__name">Doran Kelbrath</h1>
      <p class="contact__role">Partner</p>
      <ul class="contact__list">
        <li class="contact__item">
          <svg class="contact__icon" viewBox="0 0 12 12" aria-hidden="true">
            <path d="M2.2,0.8 L4,0.8 L4.8,3.2 L3.6,4.2 Q4.6,6.6 7.6,8.2 L8.7,7 L11.2,7.8 L11.2,9.8 Q11,11.2 9.6,11.2 Q1,10.5 0.8,2.2 Q0.8,0.8 2.2,0.8 Z" fill="var(--crimson)"/>
          </svg>
          <span>0461 738 524</span>
        </li>
        <li class="contact__item">
          <svg class="contact__icon" viewBox="0 0 12 12" aria-hidden="true">
            <rect x="0.5" y="2" width="11" height="8" rx="1" fill="var(--crimson)"/>
            <path d="M1.5,3 L6,6.5 L10.5,3" fill="none" stroke="var(--white)" stroke-width="1.1"/>
          </svg>
          <span>doran@kbtlaw.co</span>
        </li>
        <li class="contact__item">
          <svg class="contact__icon" viewBox="0 0 12 12" aria-hidden="true">
            <circle cx="6" cy="6" r="5.5" fill="var(--crimson)"/>
            <ellipse cx="6" cy="6" rx="2.3" ry="5.3" fill="none" stroke="var(--white)" stroke-width="0.9"/>
            <path d="M0.6,6 H11.4" stroke="var(--white)" stroke-width="0.9"/>
          </svg>
          <span>www.<span class="accent">kbtlaw</span>.co</span>
        </li>
      </ul>
    </div>

    <p class="address">Level 3, 118 Wendmore Street Sydney NSW 2000</p>
  </section>
</main>
</body>
</html>
```